verdant terraces simple classy business card design

my name is colin barrow and I run a gardening business aimed at high class verdant terraces. the business name is verdant terraces and our logo was designed on pixel harbour .My clientel are anything from residential homes to businesses. I take pride in my work and know that I offer a service like no other in my area.
The business card will be used to represent my business and I want it to be not only rememberable, but simplistic and modern. Eye catching too. Of course I would like it relatable to gardening and appealing to the correct clientel - those being garden enthusiasts, prestigious homes and businesses that are after top of the line gardening services like no other on the market.
I am not a typical lawn mowing business so I don't want a typical card design that represents that. The gardens I work with are generally million dollar properties with owners who are very garden proud looking for upkeep and guidance from me along with sometimes whole new garden designs. I want the business cards to show to my clients that I take pride, as they do, in their garden. And I want them to know from my card that I am a professional, qualified horticulturist offering them a top of the line service for life. I want them to refer my business on. I want them to look at my business card and see class and professionalism in a modern unique bold way.
The card should be simple with the possibility of the logo on the front being embossed/debossed and my details on the back the card should have a organic garden feel it's very important to me that it is absolutely perfect
I am also very open to ideas and suggestions so look forward to seeing the designs. the business logo has been supplied with this project and I want the card to be double sided

Contact info is
Colin Barrow - Managing Director / Horticulturist
Phone : 0481 526 704
Email: colinbarrow@verdantterraces.example.au

Target Market(s)

high class gardens residential and commercial

Industry/Entity Type

Gardener

Contact Information for Business Card

Contact info is
Phone : 0481 526 704

PLEASE MAKE CARD DOUBLE SIDED

Requirements
Must have
• organic simple classy modern feel
• must flow with the current logo that has been supplied with this project
• Double sided
• Must explain in a simple way that I deal with high end gardens and I'm a qualified horticulturist
Nice to have
• embossed debossed logo
Should not have
• shouldn't be to busy or cheap looking

```html
<!DOCTYPE html>
<html lang="en">
<head>
<meta charset="utf-8">
<title>Verdant Terraces – Business Card</title>
<link rel="stylesheet" href="https://fonts.googleapis.com/css2?family=Cinzel:wght@400&family=Mulish:wght@400;700&display=swap">
<style>
  :root {
    --backdrop: #2b2b2d;
    --leaf-green: #5d9e57;
    --leaf-green-soft: #e6f0e4;
    --card-white: #f7f7f5;
    --ink: #3a3a3a;
    --ink-soft: #555555;
    --on-green: #ffffff;
  }
  * { box-sizing: border-box; margin: 0; padding: 0; }
  html, body {
    width: 1200px;
    height: 800px;
    overflow: hidden;
    background: var(--backdrop);
  }
  .stage {
    position: relative;
    width: 1200px;
    height: 800px;
    display: flex;
    align-items: center;
    justify-content: center;
    gap: 48px;
  }
  .card {
    position: relative;
    width: 520px;
    height: 300px;
    border-radius: 22px;
    overflow: hidden;
    box-shadow: 0 10px 30px rgba(0,0,0,0.35);
  }

  /* Front */
  .card-front {
    background: var(--leaf-green);
    display: flex;
    align-items: center;
    justify-content: center;
  }
  .brand-lockup {
    display: flex;
    align-items: center;
    gap: 16px;
  }
  .brand-mark {
    width: 22px;
    height: 22px;
    border-radius: 50%;
    background: var(--on-green);
  }
  .brand-name {
    font-family: "Cinzel", serif;
    font-weight: 400;
    font-size: 38px;
    letter-spacing: 2px;
    color: var(--on-green);
    text-transform: uppercase;
  }

  /* Back */
  .card-back {
    background: var(--card-white);
  }
  .contact {
    position: absolute;
    left: 40px;
    top: 44px;
    width: 270px;
    font-family: "Mulish", sans-serif;
    color: var(--ink);
  }
  .contact-name {
    font-weight: 700;
    font-size: 19px;
    color: var(--ink);
  }
  .contact-title {
    font-weight: 400;
    font-size: 13px;
    color: var(--ink-soft);
    margin-top: 4px;
  }
  .contact-rule {
    height: 1px;
    background: var(--ink);
    margin: 14px 0;
  }
  .contact-line {
    display: flex;
    align-items: center;
    gap: 10px;
    font-size: 12.5px;
    color: var(--ink-soft);
    margin: 8px 0;
    white-space: nowrap;
  }
  .contact-line svg { flex: none; }
  .decor-canopy {
    position: absolute;
    right: -40px;
    top: 70px;
    width: 250px;
    height: 250px;
    border-radius: 50%;
    background: var(--leaf-green-soft);
  }
</style>
</head>
<body>
  <main class="stage">
    <section class="card card-front" aria-label="Card front">
      <div class="brand-lockup">
        <span class="brand-mark"></span>
        <span class="brand-name">Verdant Terraces</span>
      </div>
    </section>

    <section class="card card-back" aria-label="Card back">
      <div class="decor-canopy" role="img" aria-label="Large brand tree decoration in green"></div>
      <div class="contact">
        <p class="contact-name">Colin Barrow</p>
        <p class="contact-title">Managing Director / Horticulturist</p>
        <div class="contact-rule"></div>
        <p class="contact-line">
          <svg width="14" height="14" viewBox="0 0 24 24" aria-hidden="true">
            <path fill="#3a3a3a" d="M6.6 10.8a15.1 15.1 0 0 0 6.6 6.6l2.2-2.2a1 1 0 0 1 1-.25 11.4 11.4 0 0 0 3.6.57 1 1 0 0 1 1 1V20a1 1 0 0 1-1 1A17 17 0 0 1 3 4a1 1 0 0 1 1-1h3.5a1 1 0 0 1 1 1c0 1.25.2 2.45.57 3.57a1 1 0 0 1-.25 1z"/>
          </svg>
          0481 526 704
        </p>
        <p class="contact-line">
          <svg width="14" height="14" viewBox="0 0 24 24" aria-hidden="true">
            <rect x="2" y="5" width="20" height="14" rx="1.5" fill="none" stroke="#3a3a3a" stroke-width="2"/>
            <path d="M3 6l9 7 9-7" fill="none" stroke="#3a3a3a" stroke-width="2"/>
          </svg>
          colinbarrow@verdantterraces.example.au
        </p>
        <div class="contact-rule"></div>
      </div>
    </section>
  </main>
</body>
</html>
```